Norrell Advisory WA Business Card

Create an interesting, eye catching and colourful two sided business card. We are a business consulting operation assisting SME's improve all areas of their business. We provide consulting services to assist SME's to create a culture of continuous improvement, making a positive difference in the business. Our tag line is Small changes, big rewards. We want to create a well recognised, innovative brand that can be continued throughout our website, social media and email correspondence.

Target Market(s)

Small to Medium Enterprise Business Owners

Industry/Entity Type

Business Consultant

Contact Information for Business Card

Name of Business: Norrell Advisory - Small Changes Big Rewards
Derek Holloway Ph 0407385510 Megan Holloway Ph 0407913847
Email norrelladvisorywa@mailbox-example.com
Web address TBA
FaceBook page TBA

BACKSIDE OF CARD

Providing assistance with:

• Organisation & Efficiency
• Revenue generation & Marketing
• Financial Management
• Production quality & delivery
• Systems & Process documentation
• Exit Strategy

Font styles to use
Other font styles liked:
• Calibri

Colors

Designer to choose colors to be used in the design.

Requirements
Must have
• Calibri font

```html
<!DOCTYPE html>
<html lang="en">
<head>
<meta charset="utf-8">
<title>Norrell Advisory WA Business Card</title>
<link rel="stylesheet" href="https://fonts.googleapis.com/css2?family=Carlito:wght@400;700&family=Arimo:wght@400&display=swap">
<style>
  :root {
    --backdrop: #4a4b4f;
    --card: #ffffff;
    --brand-red: #e8402f;
    --brand-blue: #0b72b5;
    --sky-blue: #2a9be0;
    --tag-blue: #1670b8;
    --ink: #2a2a2a;
    --on-blue: #ffffff;
  }
  * { margin: 0; padding: 0; box-sizing: border-box; }
  html, body { width: 1200px; height: 1000px; overflow: hidden; }
  body {
    background: var(--backdrop);
    font-family: "Carlito", "Calibri", sans-serif;
    position: relative;
  }
  .card {
    position: absolute;
    left: 250px;
    width: 700px;
    height: 380px;
    background: var(--card);
    border-radius: 28px;
    overflow: hidden;
  }
  .card--back { top: 80px; }
  .card--front { top: 540px; }

  .brand {
    display: flex;
    align-items: center;
    justify-content: center;
    gap: 12px;
    white-space: nowrap;
  }
  .brand__dot {
    width: 20px; height: 20px;
    border-radius: 50%;
    background: var(--brand-red);
    flex: none;
  }
  .brand__name {
    font-weight: 700;
    color: var(--brand-red);
    text-transform: uppercase;
    letter-spacing: 1px;
    white-space: nowrap;
  }

  /* back side */
  .card--back .brand { margin-top: 120px; }
  .card--back .brand__name { font-size: 34px; }
  .mission {
    margin-top: 34px;
    text-align: center;
    color: var(--tag-blue);
    font-weight: 700;
    font-size: 20px;
    letter-spacing: 0.5px;
  }
  .services {
    margin-top: 8px;
    text-align: center;
    color: var(--ink);
    font-size: 18px;
    line-height: 1.3;
  }

  /* front side */
  .front-art { position: absolute; inset: 0; }
  .people {
    position: absolute;
    left: 56px;
    top: 56px;
    color: var(--on-blue);
  }
  .person { margin-bottom: 16px; }
  .person__name {
    font-weight: 700;
    font-size: 24px;
    text-transform: uppercase;
    letter-spacing: 0.5px;
  }
  .person__phone,
  .contact {
    display: flex;
    align-items: center;
    gap: 8px;
    font-family: "Arimo", "Arial", sans-serif;
    white-space: nowrap;
  }
  .person__phone { font-size: 20px; gap: 10px; }
  .icon { width: 16px; height: 16px; flex: none; }
  .contact .icon { width: 14px; height: 14px; }
  .contacts {
    position: absolute;
    left: 30px;
    bottom: 34px;
    color: var(--on-blue);
    font-size: 14px;
    line-height: 1.5;
  }
  .fb-dot {
    width: 10px; height: 10px;
    margin: 0 2px;
    border-radius: 50%;
    background: var(--on-blue);
    flex: none;
  }
  .front-brand {
    position: absolute;
    left: 372px;
    right: 12px;
    top: 186px;
    text-align: center;
  }
  .front-brand .brand__name { font-size: 27px; }
  .front-brand .brand__dot { width: 16px; height: 16px; }
  .tagline {
    margin-top: 4px;
    font-size: 16px;
    color: var(--ink);
    letter-spacing: 1px;
    text-transform: uppercase;
    white-space: nowrap;
  }
</style>
</head>
<body>

<section class="card card--back" aria-label="Card back">
  <div class="brand">
    <span class="brand__dot"></span>
    <span class="brand__name">Norrell Advisory</span>
  </div>
  <p class="mission">CREATING A CULTURE OF CONTINUOUS IMPROVEMENT</p>
  <p class="services">
    Organisation &amp; Efficiency | Revenue generation &amp; Marketing | Financial Management<br>
    Production quality &amp; delivery | Systems &amp; Process documentation | Exit Strategy
  </p>
</section>

<section class="card card--front" aria-label="Card front">
  <svg class="front-art" viewBox="0 0 700 380" width="700" height="380" aria-hidden="true">
    <path d="M0,0 H196 C330,70 392,220 392,380 H0 Z" fill="var(--brand-red)"/>
    <path d="M0,0 H184 C318,70 380,220 380,380 H0 Z" fill="var(--sky-blue)"/>
    <path d="M0,0 H168 C300,72 360,222 360,380 H0 Z" fill="var(--brand-blue)"/>
  </svg>

  <div class="people">
    <div class="person">
      <div class="person__name">Derek Holloway</div>
      <div class="person__phone">
        <svg class="icon" viewBox="0 0 16 16"><path d="M3 1l3 3-1.5 2a9 9 0 0 0 5.5 5.5L12 10l3 3-2 2C6 14 2 10 1 3z" fill="#fff"/></svg>
        0407385510
      </div>
    </div>
    <div class="person">
      <div class="person__name">Megan Holloway</div>
      <div class="person__phone">
        <svg class="icon" viewBox="0 0 16 16"><path d="M3 1l3 3-1.5 2a9 9 0 0 0 5.5 5.5L12 10l3 3-2 2C6 14 2 10 1 3z" fill="#fff"/></svg>
        0407913847
      </div>
    </div>
  </div>

  <div class="contacts">
    <div class="contact">
      <svg class="icon" viewBox="0 0 16 16"><rect x="1" y="3" width="14" height="10" rx="1" fill="none" stroke="#fff" stroke-width="1.5"/><path d="M1.5 4l6.5 5 6.5-5" fill="none" stroke="#fff" stroke-width="1.5"/></svg>
      norrelladvisorywa@mailbox-example.com
    </div>
    <div class="contact">
      <svg class="icon" viewBox="0 0 16 16"><circle cx="8" cy="8" r="6.5" fill="none" stroke="#fff" stroke-width="1.4"/><path d="M1.5 8h13M8 1.5c-3 3.5-3 9.5 0 13M8 1.5c3 3.5 3 9.5 0 13" fill="none" stroke="#fff" stroke-width="1.2"/></svg>
      www.norrelladvisory-example.com
    </div>
    <div class="contact">
      <span class="fb-dot"></span>
      norrelladvisory
    </div>
  </div>

  <div class="front-brand">
    <div class="brand">
      <span class="brand__dot"></span>
      <span class="brand__name">Norrell Advisory</span>
    </div>
    <p class="tagline">Small changes * Big rewards</p>
  </div>
</section>

</body>
</html>
```